Creation of an elegant and modern turnkey Shopify website

Hello,

We are a new company specializing in the sale of above-ground pools. We want to create a turnkey website, ideally using Shopify. For now, we need a "showcase" site, not an e-commerce platform, with four tabs:

Home Page (an overall presentation of the company)
Our Products (an overview of all the above-ground pools we sell)
Our Projects (a page inspired by Instagram to showcase photos of our future projects)
Contact (a page with all our contact information and a contact form)

We are looking to create a highly visual, elegant, and modern website with vibrant splashes of color. We will provide the text, photos (along with instructions on where to place them on each page), and all other necessary information as attachments.

Thank you in advance for your proposals!

The Brisa Lagoon Team

Target Market(s)

Targeted at Swiss customers (a translator will need to be installed for different languages)

Industry/Entity Type

Sale of customised above-ground pools

Coding

Coded - Design and coding required

Font styles to use
Sans Serif

Colors
0094D4
00A9DD
6FCCEA
C7EBF8
E9F6FB
00AB8E
00BBA5
67D7C9
C6EFE9
E9F9F6

Requirements
Must have
• A stunning, elegant and modern look
Nice to have
• Inspiration from the colors of our logo throughout the site, but in an elegant way
Should not have
• An overly classic look for swimming pool sites

```html
<!DOCTYPE html>
<html lang="en">
<head>
<meta charset="utf-8">
<title>Brisa Lagoon – Above-Ground Pools</title>
<link href="https://fonts.googleapis.com/css2?family=Montserrat:wght@300;400;500;600;700&display=swap" rel="stylesheet">
<style>
:root{
  --blue:#0094D4;
  --blue-bright:#00A9DD;
  --blue-soft:#6FCCEA;
  --blue-pale:#C7EBF8;
  --blue-mist:#E9F6FB;
  --ink:#1d2430;
  --text:#3b4350;
  --footer-bg:#f4f6f7;
  --white:#ffffff;
}
*{box-sizing:border-box;margin:0;padding:0}
html,body{width:1200px;height:3300px;overflow:hidden;background:var(--white)}
body{font-family:"Montserrat",sans-serif;color:var(--text);position:relative}
.abs{position:absolute}

/* header */
.site-header{left:0;top:0;width:1200px;height:100px;background:var(--white)}
.brand{left:100px;top:24px;display:flex;align-items:center;gap:10px}
.brand-dot{width:14px;height:14px;border-radius:50%;background:var(--blue-bright)}
.brand-name{font-size:26px;font-weight:500;color:var(--blue);line-height:1}
.main-nav{left:305px;top:40px;display:flex;gap:46px;font-size:14px;font-weight:600;color:var(--ink);letter-spacing:.3px}
.main-nav .active{color:var(--blue);position:relative}
.main-nav .active::after{content:"";position:absolute;left:0;right:0;top:24px;height:2px;background:var(--blue)}
.header-tools{left:930px;top:36px;display:flex;align-items:center;gap:36px;font-size:14px;font-weight:600;color:var(--ink)}

/* hero */
.hero{left:0;top:100px;width:1200px;height:520px;background:linear-gradient(160deg,#e8f3f8 0%,#bfe3f1 30%,#4fb7e0 55%,#1f8fc8 80%,#3aa7d6 100%)}
.hero-title{left:110px;top:245px;font-size:38px;font-weight:700;color:var(--ink);letter-spacing:.5px}
.hero-title span{font-weight:400}
.hero-lead{left:110px;top:308px;width:520px;font-size:16px;line-height:30px;color:var(--ink)}
.btn{left:110px;top:420px;width:230px;height:56px;border-radius:28px;background:var(--blue);color:var(--white);font-size:16px;font-weight:700;letter-spacing:.5px;display:flex;align-items:center;justify-content:center}
.arrow-btn{width:44px;height:44px;border-radius:50%;background:var(--white);display:flex;align-items:center;justify-content:center}

/* intro */
.intro-title{left:0;top:705px;width:1200px;text-align:center;font-size:30px;font-weight:700;color:var(--blue);letter-spacing:.5px;line-height:46px}
.intro-title .sub{font-weight:400;color:var(--blue-bright)}
.intro-text{left:200px;top:845px;width:800px;text-align:center;font-size:16px;line-height:31px;color:var(--ink)}
.intro-text p{margin-bottom:12px}

/* why band */
.why{left:0;top:1115px;width:1200px;height:475px;background:var(--blue)}
.why-title{left:0;top:1172px;width:1200px;text-align:center;font-size:28px;font-weight:700;color:var(--white)}
.why-title span{font-weight:400}
.feature{top:1290px;width:300px;text-align:center;color:var(--white)}
.feature svg{display:block;margin:0 auto 22px}
.feature h3{font-size:20px;font-weight:700;text-transform:uppercase;margin-bottom:16px}
.feature h3 span{font-weight:400}
.feature p{font-size:14px;line-height:28px}

/* split rows */
.row-text{width:600px;padding:0 110px}
.row-title{font-size:30px;font-weight:700;color:var(--blue);text-transform:uppercase;margin-bottom:28px}
.row-title span{font-weight:400;color:var(--blue-bright)}
.row-text p{font-size:15px;line-height:30px;color:var(--ink)}
.photo{width:600px}
.photo-a{background:linear-gradient(135deg,#7fd3ee 0%,#2fb3e2 50%,#58c3e9 100%)}
.photo-b{background:linear-gradient(120deg,#f0e2d6 0%,#e6c2aa 40%,#46b9dc 70%,#1c9ccf 100%)}
.photo-c{background:linear-gradient(150deg,#3bb4dd 0%,#1690c6 50%,#2aa6d6 100%)}

/* footer */
.site-footer{left:0;top:2900px;width:1200px;height:305px;background:var(--footer-bg)}
.footer-col h4{font-size:20px;font-weight:700;color:var(--blue);margin-bottom:24px;text-transform:uppercase}
.footer-col li{list-style:none;font-size:14px;font-weight:500;color:var(--ink);line-height:34px;text-transform:uppercase}
.contact-line{display:flex;align-items:center;gap:18px;font-size:14px;font-weight:600;color:var(--ink);text-transform:uppercase;line-height:34px}
.footer-photo{left:850px;top:2960px;width:260px;height:180px;background:linear-gradient(135deg,#5cc5ea 0%,#1e96cc 60%,#b9e4f3 100%)}
.bottom-bar{left:0;top:3205px;width:1200px;height:95px;background:var(--blue)}
.copyright{left:90px;top:3241px;font-size:13px;font-weight:600;color:var(--white)}
.social{left:950px;top:3233px;display:flex;gap:10px}
.social span{width:34px;height:34px;border-radius:50%;background:var(--white)}
</style>
</head>
<body>

<header class="site-header abs">
  <div class="brand abs"><span class="brand-dot"></span><span class="brand-name">Brisa Lagoon</span></div>
  <nav class="main-nav abs">
    <span class="active">HOME</span>
    <span>OUR PRODUCTS</span>
    <span>OUR PROJECTS</span>
    <span>CONTACT US</span>
  </nav>
  <div class="header-tools abs">
    <span>EN ▾</span>
    <svg width="20" height="20" viewBox="0 0 20 20"><circle cx="8" cy="8" r="6" fill="none" stroke="#1d2430" stroke-width="2"/><line x1="12.5" y1="12.5" x2="18" y2="18" stroke="#1d2430" stroke-width="2"/></svg>
    <svg width="24" height="22" viewBox="0 0 24 22"><path d="M1 2h4l3 12h12l3-9H7" fill="none" stroke="#1d2430" stroke-width="2"/><circle cx="10" cy="19" r="2" fill="#1d2430"/><circle cx="18" cy="19" r="2" fill="#1d2430"/></svg>
  </div>
</header>

<section class="hero abs" role="img" aria-label="Photo of a sunlit pool with a ladder and clear blue water"></section>
<h1 class="hero-title abs">WE BRING YOUR POOL <span>DREAMS TO LIFE!</span></h1>
<p class="hero-lead abs">Lorem ipsum dolor sit amet, consectetur adipiscing elit, sed do eiusmod tempor incididunt ut.</p>
<a class="btn abs">GET STARTED</a>
<div class="arrow-btn abs" style="left:24px;top:343px"><svg width="14" height="14" viewBox="0 0 14 14"><path d="M9 2L4 7l5 5" fill="none" stroke="#0094D4" stroke-width="2.5"/></svg></div>
<div class="arrow-btn abs" style="left:1132px;top:343px"><svg width="14" height="14" viewBox="0 0 14 14"><path d="M5 2l5 5-5 5" fill="none" stroke="#0094D4" stroke-width="2.5"/></svg></div>

<h2 class="intro-title abs">TRANSFORM YOUR GARDEN WITH OUR PREMIUM<br><span class="sub">ABOVE-GROUND POOLS!</span></h2>
<div class="intro-text abs">
  <p>Achieve your dreams with our custom, tailor-made above-ground pools.</p>
  <p>Imagine an exceptional relaxation and leisure space right in your own backyard. With our unparalleled expertise and commitment to excellence, we create above-ground pools that exceed all expectations.</p>
  <p>Our exclusive, custom-designed models are crafted to combine style, durability, and innovation, offering a unique and refined experience.</p>
</div>

<section class="why abs"></section>
<h2 class="why-title abs">WHY CHOOSE OUR <span>ABOVE-GROUND POOLS?</span></h2>
<svg class="abs" style="left:30px;top:1440px" width="30" height="20" viewBox="0 0 30 20"><path d="M28 10H3M10 3L3 10l7 7" fill="none" stroke="#fff" stroke-width="2.5"/></svg>
<svg class="abs" style="left:1140px;top:1440px" width="30" height="20" viewBox="0 0 30 20"><path d="M2 10h25M20 3l7 7-7 7" fill="none" stroke="#fff" stroke-width="2.5"/></svg>

<div class="feature abs" style="left:115px">
  <svg width="80" height="80" viewBox="0 0 80 80"><circle cx="40" cy="40" r="38" fill="none" stroke="#fff" stroke-width="2"/><circle cx="40" cy="34" r="13" fill="none" stroke="#fff" stroke-width="2.5"/><path d="M32 45l-4 16 12-6 12 6-4-16" fill="none" stroke="#fff" stroke-width="2.5"/></svg>
  <h3>Superior <span>Quality</span></h3>
  <p>Each pool is constructed with high-quality materials, ensuring exceptional durability and strength.</p>
</div>
<div class="feature abs" style="left:450px">
  <svg width="80" height="80" viewBox="0 0 80 80"><circle cx="40" cy="40" r="38" fill="none" stroke="#fff" stroke-width="2"/><path d="M24 28h32M26 56h28M30 30v24M40 30v24M50 30v24M28 22h24" fill="none" stroke="#fff" stroke-width="2.5"/></svg>
  <h3>Elegant <span>Design</span></h3>
  <p>Our pools come in a variety of styles and finishes, seamlessly blending into any garden setting.</p>
</div>
<div class="feature abs" style="left:785px">
  <svg width="80" height="80" viewBox="0 0 80 80"><circle cx="40" cy="40" r="38" fill="none" stroke="#fff" stroke-width="2"/><path d="M26 54l20-20M44 26a8 8 0 1 0 10 10M30 26l24 28M26 30l4-4" fill="none" stroke="#fff" stroke-width="2.5"/></svg>
  <h3>Custom &amp; <span>Tailor-Made</span></h3>
  <p>Create the pool of your dreams with our customisation options, tailored to your specific tastes and needs.</p>
</div>

<div class="row-text abs" style="left:0;top:1755px">
  <h2 class="row-title">Personalized <span>Services</span></h2>
  <p>We understand that every garden and client is unique. That's why we offer personalized services, from design to installation and after-sales support. Our team of experts is here to answer all your questions and guide you throughout your project.</p>
</div>
<div class="photo photo-a abs" style="left:600px;top:1705px;height:370px" role="img" aria-label="Photo from above of a person relaxing on a pink float in a pool"></div>

<div class="photo photo-b abs" style="left:0;top:2075px;height:365px" role="img" aria-label="Photo of a sun hat and legs resting at the edge of a pool"></div>
<div class="row-text abs" style="left:600px;top:2120px">
  <h2 class="row-title">Guaranteed <span>Satisfaction</span></h2>
  <p>Your satisfaction is our top priority. We are committed to providing you with exceptional service and the highest quality products. Join our community of satisfied customers who are already enjoying their custom above-ground pools. 10-Year Warranty!</p>
</div>

<div class="row-text abs" style="left:0;top:2495px">
  <h2 class="row-title">Contact <span>Us Today!</span></h2>
  <p>Don't wait any longer to transform your garden into a wellness oasis. Contact us today to discover our range of customizable above-ground pools and get a tailored quote. Dive into a world of infinite possibilities with Brisa Lagoon.</p>
</div>
<div class="photo photo-c abs" style="left:600px;top:2440px;height:370px" role="img" aria-label="Photo of a person floating on their back in a clear blue pool"></div>

<footer class="site-footer abs"></footer>
<div class="footer-col abs" style="left:90px;top:2955px">
  <h4>Contact Us</h4>
  <div class="contact-line"><svg width="14" height="18" viewBox="0 0 14 18"><path d="M7 17S1 10 1 6.5a6 6 0 0 1 12 0C13 10 7 17 7 17z" fill="#1d2430"/><circle cx="7" cy="6.5" r="2.2" fill="#f4f6f7"/></svg>Chemin des Tilleuls 12</div>
  <div class="contact-line" style="padding-left:32px">1820 Montreux</div>
  <div class="contact-line"><svg width="14" height="16" viewBox="0 0 14 16"><path d="M3 1l3 4-2 2c1 2 3 4 5 5l2-2 3 3-2 2C6 15-1 8 1 3z" fill="#1d2430"/></svg>079 000 12 34</div>
</div>
<div class="footer-col abs" style="left:460px;top:2955px">
  <h4>Quick Links</h4>
  <ul><li>Home</li><li>Our Products</li><li>Our Projects</li><li>Contact Us</li></ul>
</div>
<div class="footer-col abs" style="left:650px;top:2955px">
  <h4>Links</h4>
  <ul><li>Privacy Policy</li><li>Terms of Use</li><li>Blogs</li></ul>
</div>
<div class="footer-photo abs" role="img" aria-label="Collage of pool photos"></div>

<div class="bottom-bar abs"></div>
<p class="copyright abs">COPYRIGHT © 2024 . ALL RIGHTS RESERVED.</p>
<div class="social abs"><span></span><span></span><span></span><span></span><span></span></div>

</body>
</html>
```